Preisliste für Kosmetikinstitut
Zielgruppe
Ich benötige für mein Kosmetikinstitut eine Preisliste für die moderne Frau, aber auch Männer. Das Design sollte mein Logo enthalten. Farben des Designkonzepts einbauen.
A4 quer zum Falten, wie ein Heft, 1. Seite Preisliste mit logo, im Innenteil dann Anwendungen
Aufgabenstellung
Minimalistisch, ästhetisch, modern, edel
Kontaktdaten auf der Rückseite
LB Hautatelier
Lotte Brenner
Lindenhang 17
83671 Waakirchen
EMail: lotte@lb-hautatelier.de
Whatsapp: 0176 284 9017

```html
<!DOCTYPE html>
<html lang="de">
<head>
<meta charset="utf-8">
<title>LB Hautatelier – Preisliste</title>
<link rel="stylesheet" href="https://fonts.googleapis.com/css2?family=Questrial&display=swap">
<style>
  :root {
    --canvas: #ffffff;
    --cover-grey: #c6c6c6;
    --gold: #8a6d2e;
    --mauve: #9a8a8a;
  }
  html, body {
    margin: 0;
    padding: 0;
    width: 1200px;
    height: 1200px;
    overflow: hidden;
    background: var(--canvas);
  }
  .cover {
    position: absolute;
    left: 252px;
    top: 107px;
    width: 696px;
    height: 985px;
    background: var(--cover-grey);
    font-family: "Questrial", sans-serif;
    color: var(--gold);
  }
  .brand {
    position: absolute;
    left: 0;
    right: 0;
    top: 290px;
    text-align: center;
  }
  .brand-name {
    margin: 0;
    font-size: 40px;
    font-weight: 400;
    letter-spacing: 1px;
    line-height: 1;
    color: var(--gold);
    transform: translateX(30px);
  }
  .title-block {
    position: absolute;
    left: 225px;
    top: 833px;
    width: 224px;
    text-align: center;
  }
  .title-rule {
    height: 0;
    border-top: 1.5px solid var(--gold);
    margin: 0;
  }
  .title {
    margin: 10px 0 0;
    font-size: 37px;
    font-weight: 400;
    line-height: 1;
    color: var(--gold);
    transform: translateX(5px);
  }
  .title .accent { color: var(--mauve); }
</style>
</head>
<body>
  <main class="cover">
    <header class="brand">
      <p class="brand-name">LB Hautatelier</p>
    </header>
    <section class="title-block">
      <hr class="title-rule">
      <h1 class="title">Preis<span class="accent">li</span>ste</h1>
    </section>
  </main>
</body>
</html>
```